PostCard Design Project

I am making a mailing postcard
I am having the mailing printed using 4 color foil on certain parts.
I am looking for a design that maximizes the foil process where certain parts are done in foil to grab the customers attention (example: if there is a car on the postcard the headlights would be done in foil) .
I am targeting some industries, (auto, real estate, medical, beauty) I would like the post card to have examples of postcard ideas for 2 or 3 of these industries.
specs:
the postcard should be atleast 6.5x9 up to 8.5x11, I don't want to restrict the space for the creative as I don't want everything to look like a huge mess. both sides will be used.
the piece is a direct mail piece so it has to meet requirements of https://www.mailvantor.com/business/pdf/quick-reference-guide.pdf
text will be
"business with no limits, meet mailing with no addresses, gain new customers through "Open Porch Route Drop" reach new customers at their home without needing their address. "
I also want some current print specials I am running included.
-double your order FREE (order 500 business cards and get 1000)
-250 100lb gloss stock brochures 99.00
-business packages (cards, envelopes and letterhead) 299
-1000 flyers 140.40
-5000 postcards 179.99
A list of services
banners
booklets
brochures
business cards
calendars
catalogs
CD/DVD packages
envelopes
event tickets
flyers
hangtags
postcards
posters
presentation folders
rack cards
labels
table tents
window cling and decal
"order 24/7 orders@inkwillow.com" must be included
my logo is InkWillow will be supplied later
ive received some great designs. however Im looking for something a little more modern like some zorvel would put out. if the amount of words is too much please feel free to edit. also an idea i had for the list of services i offer is to have it transparent yet readable as the background of the postcard some small some big but covering the entire backgroud. you can then design on top of that with other thing. just an early morning thought
Reason: I have uploaded a sketch of my idea, please take time to look at it for an accurate depiction of what im looking for. feel free to add elements that make it pop off the page
Reason: We are getting close i will be providing feed back today

```html
<!DOCTYPE html>
<html lang="en">
<head>
<meta charset="utf-8">
<title>InkWillow Mailing Postcard</title>
<link href="https://fonts.googleapis.com/css2?family=Archivo:wght@700;800;900&family=Open+Sans:wght@400;600;700&display=swap" rel="stylesheet">
<style>
  :root {
    --brown: #4a1d0c;
    --brown-deep: #3a1507;
    --orange: #f07a1a;
    --orange-light: #f7a52a;
    --amber: #f5b532;
    --white: #ffffff;
    --ink: #2a1206;
    --line: #3b3b3b;
    --bg: #2b2b2b;
  }
  * { box-sizing: border-box; margin: 0; padding: 0; }
  html, body { width: 1200px; height: 900px; overflow: hidden; }
  body { background: var(--bg); font-family: "Open Sans", sans-serif; position: relative; }

  .postcard {
    position: absolute; top: 260px; width: 570px; height: 380px; overflow: hidden;
    background: linear-gradient(160deg, var(--amber) 0%, var(--orange-light) 40%, var(--orange) 100%);
    box-shadow: 0 10px 30px rgba(0,0,0,.5);
  }
  .postcard--front { left: 20px; }
  .postcard--back { left: 610px; }

  /* front */
  .headline-band {
    position: absolute; left: 0; top: 0; width: 100%; height: 96px;
    background: var(--brown); display: flex; align-items: center; justify-content: center;
    padding: 0 18px;
  }
  .headline {
    font-family: "Archivo", sans-serif; font-weight: 800; color: var(--white);
    font-size: 15.5px; line-height: 1.4; text-align: center;
  }
  .sample-collage {
    position: absolute; left: 110px; top: 112px; width: 200px; height: 215px;
    background: linear-gradient(135deg, #3a8fd8 0%, #e8e8ee 45%, #e24a4a 70%, #f3d13a 100%);
    transform: rotate(-8deg); border-radius: 3px;
  }
  .sample-cards {
    position: absolute; left: 360px; top: 100px; width: 95px; height: 52px;
    background: linear-gradient(135deg, #6a1a12, #2b0d08);
    transform: rotate(-12deg);
  }
  .logo-corner { position: absolute; right: 0; top: 96px; width: 150px; height: 120px; }
  .logo-text {
    position: absolute; right: 14px; top: 122px; width: 100px; text-align: center;
    font-family: "Archivo", sans-serif; font-weight: 900; font-size: 15px; line-height: 1.15; color: var(--ink);
  }
  .specials {
    position: absolute; left: 318px; top: 214px; list-style: none;
    color: var(--white); font-family: "Archivo", sans-serif; font-weight: 700; font-size: 11.5px; line-height: 1.4;
  }
  .specials li { display: flex; gap: 6px; }
  .tick { flex: none; width: 10px; height: 10px; margin-top: 3px; }
  .order-line {
    position: absolute; left: 26px; bottom: 14px;
    font-family: "Archivo", sans-serif; font-weight: 800; font-size: 20px; color: var(--white);
  }

  /* back */
  .address-panel { position: absolute; left: 300px; top: 0; width: 270px; height: 330px; background: var(--white); }
  .stamp-box {
    position: absolute; right: 18px; top: 18px; width: 62px; height: 52px; border: 1px solid var(--line);
    font-size: 8px; text-align: center; display: flex; align-items: center; justify-content: center; color: var(--ink); line-height: 1.2;
  }
  .address-lines { position: absolute; left: 24px; top: 110px; width: 222px; }
  .address-lines span { display: block; height: 1px; background: var(--line); margin-bottom: 44px; }
  .services-label {
    position: absolute; left: 34px; top: 48px; background: var(--brown);
    color: var(--white); font-size: 17px; font-weight: 400; padding: 4px 14px;
  }
  .services {
    position: absolute; top: 96px; list-style: none; color: var(--ink);
    font-size: 12.5px; line-height: 1.45; font-weight: 400;
  }
  .services--a { left: 34px; }
  .services--b { left: 160px; }
  .services li { display: flex; gap: 6px; }
  .services .tick { margin-top: 4px; }
  .footer-band {
    position: absolute; left: 0; bottom: 0; width: 100%; height: 50px; background: var(--brown);
    display: flex; align-items: center; justify-content: flex-end; padding-right: 20px;
    font-family: "Archivo", sans-serif; font-weight: 800; font-size: 19px; color: var(--white);
  }
</style>
</head>
<body>
<svg width="0" height="0" style="position:absolute">
  <symbol id="tick" viewBox="0 0 10 10"><path d="M1 5 L4 8 L9 2" fill="none" stroke="currentColor" stroke-width="2"/></symbol>
</svg>

<section class="postcard postcard--front">
  <div class="headline-band">
    <p class="headline">“ Business with no limits, meet mailing with no addresses,<br>Gain new customers through “Open Porch Route Drop”<br>Reach new customers at their home without needing their address. ”</p>
  </div>
  <div class="sample-collage" role="img" aria-label="Fanned stack of sample flyers and brochures"></div>
  <div class="sample-cards" role="img" aria-label="Stack of sample business cards"></div>
  <svg class="logo-corner" viewBox="0 0 150 120" aria-hidden="true">
    <path d="M150 0 H40 Q0 50 30 120 H150 Z" fill="var(--brown)"/>
    <path d="M150 0 H50 Q14 52 42 120 H150 Z" fill="var(--white)"/>
  </svg>
  <p class="logo-text">YOUR LOGO HERE</p>
  <ul class="specials">
    <li><svg class="tick"><use href="#tick"/></svg>Double your order FREE<br>(order 500 business cards and get 1000)</li>
    <li><svg class="tick"><use href="#tick"/></svg>250 100lb gloss stock brochures 99.00</li>
    <li><svg class="tick"><use href="#tick"/></svg>business packages<br>(cards, envelopes and letterhead) 299</li>
    <li><svg class="tick"><use href="#tick"/></svg>1000 flyers 140.40</li>
    <li><svg class="tick"><use href="#tick"/></svg>5000 postcards 179.99</li>
  </ul>
  <p class="order-line">order 24/7 orders@inkwillow.com</p>
</section>

<section class="postcard postcard--back">
  <div class="address-panel">
    <div class="stamp-box">Postage<br>Stamp</div>
    <div class="address-lines"><span></span><span></span><span></span><span></span></div>
  </div>
  <h2 class="services-label">Our Services Are</h2>
  <ul class="services services--a">
    <li><svg class="tick"><use href="#tick"/></svg>banners</li>
    <li><svg class="tick"><use href="#tick"/></svg>booklets</li>
    <li><svg class="tick"><use href="#tick"/></svg>brochures</li>
    <li><svg class="tick"><use href="#tick"/></svg>business cards</li>
    <li><svg class="tick"><use href="#tick"/></svg>calendars</li>
    <li><svg class="tick"><use href="#tick"/></svg>catalogs</li>
    <li><svg class="tick"><use href="#tick"/></svg>CD/DVD packages</li>
    <li><svg class="tick"><use href="#tick"/></svg>envelopes</li>
    <li><svg class="tick"><use href="#tick"/></svg>event tickets</li>
  </ul>
  <ul class="services services--b">
    <li><svg class="tick"><use href="#tick"/></svg>flyers</li>
    <li><svg class="tick"><use href="#tick"/></svg>hangtags</li>
    <li><svg class="tick"><use href="#tick"/></svg>postcards</li>
    <li><svg class="tick"><use href="#tick"/></svg>posters</li>
    <li><svg class="tick"><use href="#tick"/></svg>presentation folders</li>
    <li><svg class="tick"><use href="#tick"/></svg>rack cards</li>
    <li><svg class="tick"><use href="#tick"/></svg>labels</li>
    <li><svg class="tick"><use href="#tick"/></svg>table tents</li>
    <li><svg class="tick"><use href="#tick"/></svg>window cling and decal</li>
  </ul>
  <div class="footer-band">order 24/7 orders@inkwillow.com</div>
</section>
</body>
</html>
```